Looking for a cool & simple business-card-design for digital agency

Hi!

We are a web agency that offers Reputation Management, Vextor & Seo Services and software development. We like cool things, we like innovative styles.

We have uploaded our logo.

Project Deadline Extended Reason: Client does not want any designs with the colorful logo. Please send us submissions ONLY with the blac and white logo. What the client would like to see:1) Back of the card: is a silver logo on a black background2) front of the card with all the data, please use white background and black logo thank you Added Friday, May 8, 2015

Industry/Entity Type

Software

```html
<!DOCTYPE html>
<html lang="de">
<head>
<meta charset="utf-8">
<title>Nordwerk AG – Stationery</title>
<link href="https://fonts.googleapis.com/css2?family=Lato:wght@400;700;900&display=swap" rel="stylesheet">
<style>
:root{
  --bg:#e9e9e9;
  --ink:#0b0b0b;
  --paper:#ffffff;
  --grey-text:#4a4a4a;
  --rule:#2a2a2a;
  --pill:#a9a9a9;
  --silver:#d8d8d8;
}
*{margin:0;padding:0;box-sizing:border-box}
html,body{width:1200px;height:1200px;overflow:hidden;background:var(--bg);font-family:"Lato",sans-serif;color:var(--ink)}
.canvas{position:relative;width:1200px;height:1200px}
.sheet{position:absolute;box-shadow:0 2px 6px rgba(0,0,0,.18)}
.brand{display:flex;flex-direction:column;align-items:flex-start}
.brand-name{font-family:"Lato",sans-serif;font-weight:900;line-height:1;letter-spacing:.5px;white-space:nowrap}
.brand-tag{font-family:"Lato",sans-serif;font-weight:400;text-transform:uppercase;line-height:1;margin-top:4px;white-space:nowrap}
.brand-row{display:flex;align-items:center;gap:8px}
.brand-mark{background:currentColor;flex:none}

/* folder */
.folder{left:242px;top:103px;width:426px;height:600px;background:var(--ink);color:var(--paper);display:flex;align-items:center;justify-content:center;border-bottom:2px solid #6b1d1d}
.folder .brand-name{font-size:36px}
.folder .brand-tag{font-size:13px;letter-spacing:4.2px;margin-top:6px}
.folder .brand-mark{width:22px;height:22px}

/* letterhead */
.letterhead{left:690px;top:103px;width:428px;height:600px;background:var(--paper)}
.lh-header{position:absolute;left:0;right:0;top:22px;display:flex;justify-content:center}
.lh-header .brand-name{font-size:16px}
.lh-header .brand-tag{font-size:7px;letter-spacing:2.2px;margin-top:2px}
.lh-header .brand-mark{width:10px;height:10px}
.lh-rule{position:absolute;left:0;right:0;top:57px;border-top:1px solid var(--rule)}
.lh-body{position:absolute;left:48px;right:30px;top:170px;font-size:6.7px;line-height:1.38;color:var(--grey-text);text-align:justify}
.lh-body p{margin-bottom:9px}
.lh-footer{position:absolute;left:0;right:0;bottom:0;height:48px;border-top:1px solid var(--rule);display:flex;align-items:center;font-size:7px;color:var(--ink)}
.lh-footer .col{padding:0 20px}
.lh-footer .col+.col{border-left:1px solid #777}
.who{font-weight:700;font-size:8px}
.who small{display:block;font-weight:400;font-size:7px}
.contact-line{display:flex;align-items:center;gap:4px;line-height:1.4;white-space:nowrap}
.icon{width:7px;height:7px;fill:var(--ink);flex:none}

/* business cards */
.card{left:102px;width:336px;height:201px}
.card-front{top:743px;background:var(--paper)}
.card-front .card-logo{position:absolute;left:0;right:0;top:34px;display:flex;justify-content:center}
.card-front .brand-name{font-size:22px}
.card-front .brand-tag{font-size:9px;letter-spacing:3px}
.card-front .brand-mark{width:14px;height:14px}
.name-pill{position:absolute;left:84px;top:98px;width:168px;height:28px;border-radius:14px;background:var(--pill);display:flex;align-items:center;justify-content:center;gap:8px;font-size:11px;white-space:nowrap}
.name-pill strong{font-weight:700}
.name-pill .sep{width:1px;height:16px;background:var(--ink)}
.card-contacts{position:absolute;left:12px;right:12px;top:148px;display:flex;justify-content:space-between;font-size:9.5px}
.card-contacts .icon{width:9px;height:9px}
.card-band{position:absolute;left:0;right:0;bottom:0;height:22px;background:var(--ink)}

.card-back{top:970px;background:var(--ink);color:var(--silver)}
.card-back .card-logo{position:absolute;left:22px;top:56px}
.card-back .brand-row{gap:12px}
.card-back .brand-name{font-size:24px;color:var(--paper)}
.card-back .brand-tag{font-size:9.5px;letter-spacing:3.2px;color:var(--paper)}
.card-back .brand-mark{width:44px;height:44px;color:var(--paper)}
.services{position:absolute;left:78px;right:16px;top:122px;font-size:9.5px;line-height:1.35;text-align:center;color:var(--silver)}

/* envelope */
.envelope{left:583px;top:743px;width:535px;height:374px;background:var(--paper);overflow:hidden}
.flap{position:absolute;left:0;top:0;width:100%;height:114px;background:var(--ink);border-radius:48px 48px 0 0}
.env-brand{position:absolute;left:30px;top:145px}
.env-brand .brand-name{font-size:17px}
.env-brand .brand-tag{font-size:7.5px;letter-spacing:2.4px;margin-top:2px}
.env-brand .brand-mark{width:11px;height:11px}
.env-address{position:absolute;right:24px;top:141px;font-size:8px;line-height:1.3;text-align:right}
.env-footer{position:absolute;left:0;right:0;bottom:0;height:36px;border-top:1px solid var(--rule);display:flex;align-items:center;gap:32px;padding-left:30px;font-size:7.5px}
</style>
</head>
<body>
<svg width="0" height="0" style="position:absolute" aria-hidden="true">
  <symbol id="i-phone" viewBox="0 0 10 10"><path d="M1 2c0-1 1-1.5 2-1.5h4C8 .5 9 1 9 2v1H6.5V2h-3v1H1zM2 4h6l1 5H1z"/></symbol>
  <symbol id="i-mail" viewBox="0 0 10 10"><path d="M0 2h10v6H0zM.8 2.6 5 5.6l4.2-3H.8z" fill-rule="evenodd"/></symbol>
  <symbol id="i-web" viewBox="0 0 10 10"><circle cx="5" cy="5" r="4.5"/><path d="M1 5h8M5 .5v9M5 .5C3 3 3 7 5 9.5M5 .5C7 3 7 7 5 9.5" stroke="#fff" stroke-width=".7" fill="none"/></symbol>
</svg>

<main class="canvas">

  <section class="sheet folder">
    <div class="brand-row">
      <span class="brand-mark"></span>
      <div class="brand">
        <span class="brand-name">Nordwerk AG</span>
        <span class="brand-tag">Digitale Strategien</span>
      </div>
    </div>
  </section>

  <section class="sheet letterhead">
    <header class="lh-header">
      <div class="brand-row">
        <span class="brand-mark"></span>
        <div class="brand">
          <span class="brand-name">Nordwerk AG</span>
          <span class="brand-tag">Digitale Strategien</span>
        </div>
      </div>
    </header>
    <div class="lh-rule"></div>
    <div class="lh-body">
      <p>Dear Tom Berg,</p>
      <p>We are pleased to confirm the start of our new digital strategy project with your team. Over the coming weeks we will review your current online presence, search rankings and customer reviews, and then prepare a clear plan with practical steps. Our developers will also assess the technical state of your website and suggest improvements where needed. We look forward to a productive collaboration and will keep you informed at each stage.</p>
      <p>Please send us access to your analytics account and a short list of your main competitors, so that we can prepare the first report before our next meeting.</p>
      <p>Once the first report is ready, we will present our findings in a short workshop and agree on priorities together. This includes reputation monitoring, content updates, search optimisation and any software work your team requires. Every task will have a clear owner and timeline, and we will share progress in a simple monthly summary. If you have questions at any point, our team is always happy to help and respond quickly.</p>
      <p>Your Sincerely</p>
    </div>
    <footer class="lh-footer">
      <div class="col who">Lena Marsh<small>Director</small></div>
      <div class="col">
        <div class="contact-line"><svg class="icon"><use href="#i-phone"/></svg>000 555 0199</div>
        <div class="contact-line"><svg class="icon"><use href="#i-mail"/></svg>info@nordwerkag.com</div>
        <div class="contact-line"><svg class="icon"><use href="#i-web"/></svg>www.nordwerkag.com</div>
      </div>
      <div class="col">Addreess Line One , Suit #1111<br>Address Line Two</div>
    </footer>
  </section>

  <section class="sheet card card-front">
    <div class="card-logo">
      <div class="brand-row">
        <span class="brand-mark"></span>
        <div class="brand">
          <span class="brand-name">Nordwerk AG</span>
          <span class="brand-tag">Digitale Strategien</span>
        </div>
      </div>
    </div>
    <div class="name-pill"><strong>Lena Marsh</strong><span class="sep"></span><span>Director</span></div>
    <div class="card-contacts">
      <span class="contact-line"><svg class="icon"><use href="#i-phone"/></svg>000 555 0199</span>
      <span class="contact-line"><svg class="icon"><use href="#i-mail"/></svg>info@nordwerkag.com</span>
      <span class="contact-line"><svg class="icon"><use href="#i-web"/></svg>www.nordwerkag.com</span>
    </div>
    <div class="card-band"></div>
  </section>

  <section class="sheet card card-back">
    <div class="card-logo">
      <div class="brand-row">
        <span class="brand-mark"></span>
        <div class="brand">
          <span class="brand-name">Nordwerk AG</span>
          <span class="brand-tag">Digitale Strategien</span>
        </div>
      </div>
    </div>
    <p class="services">Reputation Management, Vextor &amp; Seo Services<br>and Software development.</p>
  </section>

  <section class="sheet envelope">
    <div class="flap"></div>
    <div class="env-brand">
      <div class="brand-row">
        <span class="brand-mark"></span>
        <div class="brand">
          <span class="brand-name">Nordwerk AG</span>
          <span class="brand-tag">Digitale Strategien</span>
        </div>
      </div>
    </div>
    <div class="env-address">Addreess Line One , Suit #1111<br>Address line Two</div>
    <footer class="env-footer">
      <span class="contact-line"><svg class="icon"><use href="#i-phone"/></svg>000 555 0199</span>
      <span class="contact-line"><svg class="icon"><use href="#i-mail"/></svg>info@nordwerkag.com</span>
      <span class="contact-line"><svg class="icon"><use href="#i-web"/></svg>www.nordwerkag.com</span>
    </footer>
  </section>

</main>
</body>
</html>
```